Quote Cards With KB May 2025 for Instagram

I would like to put these quotes over one of the pictures attached; Instagram (new size: 4:5 (1080 x 1350 pixels) One Quote per picture, and I want the quote to be bold or easy to read as well. I provided a few reference graphics that I really like as examples below. In very small letters at the bottom add @KBHarlowOnline

All of the pictures are attached; you can pick any photo and add one quote to it; but no stock photography

```html
<!DOCTYPE html>
<html lang="en">
<head>
<meta charset="utf-8">
<title>KB Quote Cards — May 2025</title>
<link href="https://fonts.googleapis.com/css2?family=Poppins:wght@500;700;800;900&display=swap" rel="stylesheet">
<style>
  :root {
    --bg: #e6e6e6;
    --card: #141414;
    --ink: #ffffff;
    --muted: #8f8f8f;
    --handle: #d4d4d4;
    --glow: #8a8a8a;
    --mid: #3c3c3c;
    --dark: #121212;
  }
  * { box-sizing: border-box; margin: 0; padding: 0; }
  html, body { width: 1200px; height: 376px; overflow: hidden; background: var(--bg); }
  body { font-family: "Poppins", sans-serif; }

  .card {
    position: absolute; top: 113px; width: 109px; height: 141px;
    background: var(--card); overflow: hidden;
    box-shadow: 0 1px 4px rgba(0,0,0,.3);
  }
  .card--1 { left: 24px; }  .card--2 { left: 140px; } .card--3 { left: 256px; }
  .card--4 { left: 376px; } .card--5 { left: 498px; } .card--6 { left: 612px; }
  .card--7 { left: 728px; } .card--8 { left: 843px; } .card--9 { left: 959px; }
  .card--10 { left: 1074px; }

  .photo { position: absolute; inset: 0; }
  .photo--right {
    background:
      radial-gradient(ellipse 30% 60% at 74% 48%, var(--glow) 0%, rgba(90,90,90,.55) 45%, transparent 100%),
      linear-gradient(90deg, var(--dark) 0%, #1d1d1d 40%, var(--mid) 70%, #2a2a2a 100%);
  }
  .photo--left {
    background:
      radial-gradient(ellipse 30% 60% at 26% 48%, var(--glow) 0%, rgba(90,90,90,.55) 45%, transparent 100%),
      linear-gradient(270deg, var(--dark) 0%, #1d1d1d 40%, var(--mid) 70%, #2a2a2a 100%);
  }
  .photo--center {
    background:
      radial-gradient(ellipse 38% 40% at 50% 30%, var(--glow) 0%, rgba(90,90,90,.5) 50%, transparent 100%),
      linear-gradient(180deg, #4a4a4a 0%, var(--mid) 40%, #1a1a1a 65%, var(--dark) 100%);
  }
  .photo--crowd {
    background:
      radial-gradient(ellipse 60% 35% at 50% 28%, #a8a8a8 0%, #707070 50%, transparent 100%),
      linear-gradient(180deg, #8a8a8a 0%, #5a5a5a 40%, #1e1e1e 66%, var(--dark) 100%);
  }

  .copy { position: absolute; inset: 0; color: var(--ink); }
  .copy > * { position: absolute; white-space: nowrap; }

  .headline {
    font-weight: 800; font-size: 7px; line-height: 6.05px;
    text-transform: uppercase; letter-spacing: -.15px;
  }
  .headline .soft { color: var(--muted); }
  .tagline {
    font-weight: 700; font-size: 4.7px; line-height: 6px;
    letter-spacing: .8px; text-transform: uppercase;
  }
  .handle { font-weight: 500; font-size: 3.5px; color: var(--handle); }

  .centered > * { left: 0; right: 0; text-align: center; }

  .card--1 .headline { top: 91px; } .card--1 .tagline { top: 118px; } .card--1 .handle { top: 128px; }
  .card--2 .copy > * { left: 9px; }
  .card--2 .headline { top: 29px; } .card--2 .tagline { top: 100px; } .card--2 .handle { top: 125px; }
  .card--3 .copy > * { left: 58px; }
  .card--3 .headline--a { top: 29px; } .card--3 .headline--b { top: 82px; } .card--3 .handle { top: 124px; }
  .card--4 .copy > * { left: 9px; }
  .card--4 .headline { top: 30px; } .card--4 .tagline { top: 100px; } .card--4 .handle { top: 123px; }
  .card--5 .headline { top: 83px; } .card--5 .tagline { top: 115px; } .card--5 .handle { top: 127px; }
  .card--6 .copy > * { left: 52px; }
  .card--6 .headline { top: 32px; } .card--6 .tagline { top: 98px; } .card--6 .handle { top: 118px; }
  .card--7 .headline { top: 86px; } .card--7 .tagline { top: 117px; } .card--7 .handle { top: 127px; }
  .card--8 .copy > * { left: 51px; }
  .card--8 .headline { top: 26px; } .card--8 .tagline { top: 93px; } .card--8 .handle { top: 111px; }
  .card--9 .copy > * { left: 14px; }
  .card--9 .headline--a { top: 25px; } .card--9 .headline--b { top: 85px; } .card--9 .handle { top: 118px; }
  .card--10 .copy > * { left: 55px; }
  .card--10 .headline--a { top: 22px; } .card--10 .headline--b { top: 88px; } .card--10 .handle { top: 116px; }
</style>
</head>
<body>
<main class="strip">

  <article class="card card--1">
    <div class="photo photo--crowd" role="img" aria-label="Black and white photo of KB smiling courtside among a crowd"></div>
    <div class="copy centered">
      <p class="headline"><span class="soft">Tired. Moody.<br>Stubborn belly fat.</span><br>Your hormones are<br>screaming for help!</p>
      <p class="tagline">Let’s fix that.</p>
      <p class="handle">@KBHarlowOnline</p>
    </div>
  </article>

  <article class="card card--2">
    <div class="photo photo--right" role="img" aria-label="Black and white photo of KB in a sheer top, standing at right"></div>
    <div class="copy">
      <p class="headline"><span class="soft">That<br>stubborn<br>weight?<br>It’s not<br>your fault.</span><br>Your<br>hormones<br>are to blame<br>and you’re<br>not alone;</p>
      <p class="tagline">But there<br>is a fix.</p>
      <p class="handle">@KBHarlowOnline</p>
    </div>
  </article>

  <article class="card card--3">
    <div class="photo photo--left" role="img" aria-label="Black and white photo of KB smiling, hand on hip, at left"></div>
    <div class="copy">
      <p class="headline headline--a"><span class="soft">Your<br>belly isn’t<br>fat…</span><br>It’s<br>hormonal.<br>And here’s<br>how to<br>fix it.</p>
      <p class="headline headline--b">Comment<br><span class="soft">hormones</span><br>if nothing<br>is working.</p>
      <p class="handle">@KBHarlowOnline</p>
    </div>
  </article>

  <article class="card card--4">
    <div class="photo photo--right" role="img" aria-label="Black and white photo of KB in a fitted dress, at right"></div>
    <div class="copy">
      <p class="headline"><span class="soft">The<br>stubborn<br>belly fat<br>after 40?</span><br>It’s not<br>about<br>calories;<br>it’s about<br>your<br>hormones.</p>
      <p class="tagline">Here is the fix!</p>
      <p class="handle">@KBHarlowOnline</p>
    </div>
  </article>

  <article class="card card--5">
    <div class="photo photo--center" role="img" aria-label="Black and white photo of KB in a kitchen pointing down at her waist"></div>
    <div class="copy centered">
      <p class="headline"><span class="soft">Flat tummy<br>in your 40s?</span><br>It’s still possible!<br>Comment <span class="soft">bye belly</span><br>to get the 10 secrets</p>
      <p class="tagline">To a flatter tummy</p>
      <p class="handle">@KBHarlowOnline</p>
    </div>
  </article>

  <article class="card card--6">
    <div class="photo photo--left" role="img" aria-label="Black and white photo of KB standing among flowers, at left"></div>
    <div class="copy">
      <p class="headline"><span class="soft">Bloating.<br>Muffin top.<br>Puffy<br>waistline.</span><br>Your<br>body’s<br>screaming<br>for a<br>different<br>kind of fix.</p>
      <p class="tagline">Here it is.</p>
      <p class="handle">@KBHarlowOnline</p>
    </div>
  </article>

  <article class="card card--7">
    <div class="photo photo--center" role="img" aria-label="Black and white photo of KB dancing in a kitchen in a crop top"></div>
    <div class="copy centered">
      <p class="headline"><span class="soft">You’re doing<br>all the “right” things,</span><br>but your belly<br>won’t go down?<br>Here’s what</p>
      <p class="tagline">You haven’t tried.</p>
      <p class="handle">@KBHarlowOnline</p>
    </div>
  </article>

  <article class="card card--8">
    <div class="photo photo--left" role="img" aria-label="Black and white photo of KB posing outdoors, at left"></div>
    <div class="copy">
      <p class="headline"><span class="soft">This<br>90-day<br>plan helped<br>women<br>over 40</span><br>slim down,<br>get a tiny<br>waist and<br>feel sexy<br>again.</p>
      <p class="tagline">You’re next.</p>
      <p class="handle">@KBHarlowOnline</p>
    </div>
  </article>

  <article class="card card--9">
    <div class="photo photo--right" role="img" aria-label="Black and white photo of KB in a sheer top, posing at right"></div>
    <div class="copy">
      <p class="headline headline--a"><span class="soft">This is<br>the secret<br>women<br>over 40</span><br>are using<br>to get<br>snatched;<br>without<br>starving.</p>
      <p class="headline headline--b">Comment<br><span class="soft">skinny</span><br>to get the<br>exact plan.</p>
      <p class="handle">@KBHarlowOnline</p>
    </div>
  </article>

  <article class="card card--10">
    <div class="photo photo--left" role="img" aria-label="Black and white photo of KB standing full length by a city window, at left"></div>
    <div class="copy">
      <p class="headline headline--a"><span class="soft">What<br>worked<br>in your<br>30s</span><br>won’t<br>work now.<br>Here’s<br>what<br>actually<br>does.</p>
      <p class="headline headline--b">Drop<br><span class="soft">30 pounds</span><br>in 3 months.</p>
      <p class="handle">@KBHarlowOnline</p>
    </div>
  </article>

</main>
</body>
</html>
```